Cleaning Service Company In need of Good Web presence.

The company is a cleaning service company which provides professional staff and service for cleaning. This is a project to build a site that is both solid and a strong recognition of our organization. It is supposed to show quality, cleanliness, professionalism. The use of images and art for imagery is all good just to have a site that is consistent and solid. There might be a chance to make stationary, logo and business cars if someone feels they can build a brand that is consistent. The image we are going for is clean solid and to stand out. Finally stationary should not be expensive to print.

Current logo is attached and can be used or can be made more creative.

Target Market(s)

Corporate and Government entities, that will feel that this company has a brand that sets it apart from the rest. The company is new so the modification of the logo will not be an issue if a more solid brand come out of this project. The idea is to have a clean consistent product that stands our from others in terms of website, stationary, etc

Industry/Entity Type

Cleaning Service

Contact Information for Business Card

P.O.Box 51947
Riffa
Kingdom of Bahrain

Logo Text

Harbor Lane Services

Number of Pages Required

4 page

Font styles to use
Sans Serif

Colors
abd036
cadf82
eaf2ce
9bcb3b

Requirements
Must have
• Green Color to be used in order to stick to the name. Also the creativity and boldness in an elegant manner.
Nice to have
• Arabic name of company
• هاربر لين سرفسس ذ.م.م
• if cannot be put at least make a location should be chosen
• Also could be a bit of 3D given to the logo if it could stay elegent.
Should not have
• Should not show people cleaning.

```html
<!DOCTYPE html>
<html lang="en">
<head>
<meta charset="utf-8">
<title>Harbor Lane Services W.L.L</title>
<link href="https://fonts.googleapis.com/css2?family=Hind:wght@500;600&family=Questrial&family=Open+Sans:wght@400;600&family=Cairo:wght@500&display=swap" rel="stylesheet">
<style>
:root{
  --green:#9bcb3b;
  --green-strong:#abd036;
  --green-soft:#cadf82;
  --green-pale:#eaf2ce;
  --grey-icon:#c9c9c9;
  --text:#555;
  --heading:#5a5a5a;
  --dark:#2b2b2b;
  --white:#fff;
}
*{margin:0;padding:0;box-sizing:border-box}
html,body{width:1200px;height:2913px;overflow:hidden}
body{position:relative;background:var(--white);font-family:"Questrial",sans-serif;color:var(--text)}
.abs{position:absolute}

/* header */
.site-header{top:0;left:0;width:1200px;height:172px;background:var(--white);z-index:2;box-shadow:0 14px 22px -10px rgba(0,0,0,.35)}
.brand{left:88px;top:40px;display:flex;align-items:center;gap:14px}
.brand-mark{width:70px;height:70px;border-radius:50%;background:var(--green)}
.brand-name{font-family:"Questrial",sans-serif;font-size:24px;color:var(--green);line-height:1.15;width:150px}
.contact-bar{right:88px;top:42px;display:flex;gap:28px;font-size:19px;color:#444}
.contact-bar span{display:flex;align-items:center;gap:12px}
.contact-bar svg{width:34px;height:34px}
.main-nav{right:88px;top:88px;display:flex;align-items:center;gap:30px;font-size:14px;letter-spacing:.5px;color:#666}
.btn-quote{background:var(--green);color:var(--white);border-radius:22px;padding:12px 26px;font-size:14px}

/* hero */
.hero{top:172px;left:0;width:1200px;height:404px;background:var(--green)}
.hero-title{left:88px;top:125px;font-family:"Cairo",sans-serif;font-size:34px;color:var(--white)}
.hero-text{left:88px;top:183px;width:390px;font-size:13px;line-height:21px;color:var(--white)}
.btn-white{background:var(--white);color:#555;border-radius:22px;font-size:13px;text-align:center;box-shadow:0 4px 8px rgba(0,0,0,.15)}
.hero .btn-white{left:88px;top:262px;width:128px;height:42px;line-height:42px}
.hero-art{left:560px;top:62px;width:590px;height:282px;border-radius:8px;background:linear-gradient(135deg,#f4d23a 0%,#f4d23a 45%,#e9504f 70%,#dfe9c0 100%)}
.hero-dot{width:17px;height:17px;border:2px solid #5a7a1c;border-radius:50%;left:1147px}

/* services */
.section-title{width:1200px;left:0;text-align:center;font-family:"Hind",sans-serif;font-weight:600;font-size:36px;color:var(--heading)}
.title-rule{width:76px;height:3px;background:var(--green);left:562px}
.quote{width:1200px;left:0;text-align:center;font-style:italic;font-size:13px;line-height:26px;color:#444}
.service{width:330px;height:436px;top:836px;text-align:center}
.service.is-active{background:var(--white);box-shadow:0 2px 14px rgba(0,0,0,.3)}
.service-icon{width:168px;height:168px;margin:26px auto 0;border-radius:50%;border:5px solid #ddd;background:var(--grey-icon);display:flex;align-items:center;justify-content:center}
.is-active .service-icon{background:var(--green);border-color:var(--green-pale)}
.service h3{margin-top:38px;font-family:"Hind",sans-serif;font-weight:500;font-size:18px;letter-spacing:.5px;color:#444}
.service p{margin:12px auto 0;width:270px;font-size:13px;line-height:20px;color:#555}
.btn-more{display:inline-block;margin-top:32px;width:110px;height:40px;line-height:40px;border-radius:20px;background:var(--green-soft);font-size:13px;color:#444}
.is-active .btn-more{background:var(--green);color:var(--white)}

/* about */
.about{top:1382px;left:0;width:1200px;height:598px;background:radial-gradient(ellipse at 85% 80%,#a4d449 0%,transparent 45%),radial-gradient(ellipse at 20% 70%,#94c63c 0%,transparent 50%),linear-gradient(135deg,#a7d24e,#8fc53a)}
.about .section-title{color:var(--white);top:70px}
.about .quote{color:var(--white);top:142px}
.about-text{left:150px;width:900px;text-align:center;font-size:12.5px;line-height:21px;color:var(--white)}
.about .btn-white{left:537px;top:474px;width:128px;height:42px;line-height:42px;background:var(--green-pale)}

/* news */
.news-card{top:2127px;height:204px;border:1px solid #ddd;background:var(--white);display:flex}
.news-photo{width:245px;height:202px;position:relative}
.news-date{position:absolute;right:0;top:0;background:var(--green);color:var(--white);padding:4px 8px;display:flex;align-items:center;gap:4px}
.news-date b{font-family:"Open Sans",sans-serif;font-size:26px;font-weight:600}
.news-date small{font-size:11px;line-height:13px}
.news-body{padding:22px 20px}
.news-body h4{font-family:"Open Sans",sans-serif;font-weight:400;font-size:19px;line-height:25px;color:#222}
.news-body p{margin-top:8px;font-size:12.5px;line-height:19px;color:#666}

/* footer */
.site-footer{top:2413px;left:0;width:1200px;height:422px;background:var(--dark);color:var(--white)}
.footer-head{font-size:17px;letter-spacing:.5px}
.contact-item{left:88px;display:flex;align-items:center;gap:24px;font-size:13px;line-height:20px}
.contact-item .round{width:38px;height:38px;border:2px solid var(--white);border-radius:50%;display:flex;align-items:center;justify-content:center}
.social{left:88px;top:333px;display:flex;gap:6px}
.social span{width:34px;height:34px;border:2px solid var(--white);border-radius:50%}
.field{background:var(--white);color:#555;font-size:11px;padding:9px 8px;height:34px}
.btn-submit{left:1026px;top:293px;width:88px;height:42px;border:1px solid var(--white);text-align:center;line-height:40px;font-size:15px}
.bottom-bar{top:2835px;left:0;width:1200px;height:78px;background:var(--green);color:var(--white);font-size:11px}
.bottom-nav{left:86px;top:32px;display:flex;gap:30px;letter-spacing:.5px}
.copyright{right:74px;top:32px}
</style>
</head>
<body>

<header class="abs site-header">
  <div class="abs brand"><span class="brand-mark"></span><span class="brand-name">Harbor Lane Services</span></div>
  <div class="abs contact-bar">
    <span><svg viewBox="0 0 34 34"><circle cx="17" cy="17" r="17" fill="#9bcb3b"/><path d="M12 9c1 0 2 3 2 4s-2 1-1 3 3 4 5 5 2-1 3-1 4 1 4 2-2 3-4 3C15 25 9 19 9 13c0-2 2-4 3-4z" fill="#fff"/></svg>+1 555-30-7716</span>
    <span><svg viewBox="0 0 34 34"><circle cx="17" cy="17" r="17" fill="#9bcb3b"/><rect x="9" y="11" width="16" height="12" rx="1" fill="#fff"/><path d="M9 12l8 6 8-6" stroke="#9bcb3b" stroke-width="1.6" fill="none"/></svg>hello@harborlane.example</span>
  </div>
  <nav class="abs main-nav"><span>HOME</span><span>ABOUT US</span><span>STAFF</span><span>BLOG</span><span>CONTACTS</span><span class="btn-quote">GET A QUOTE</span></nav>
</header>

<section class="abs hero">
  <h1 class="abs hero-title" dir="rtl">هاربر لين سرفسس ذ.م.م</h1>
  <p class="abs hero-text">Lorem Ipsum is simply dummy text of the printing and typesetting industry. Lorem Ipsum has been the industry's standard dummy text ever since the 1500s.</p>
  <span class="abs btn-white">ABOUT ME</span>
  <div class="abs hero-art" role="img" aria-label="Illustration of a cleaning trolley, bucket, mop and dustpan"></div>
  <span class="abs hero-dot" style="top:171px"></span>
  <span class="abs hero-dot" style="top:212px"></span>
</section>

<h2 class="abs section-title" style="top:665px">Our Services</h2>
<div class="abs title-rule" style="top:720px"></div>
<p class="abs quote" style="top:745px">"Neque porro quisquam est qui dolorem ipsum quia dolor sit amet, consectetur, adipisci velit.."<br>"There is no one who loves pain itself, who seeks after it and wants to have it, simply because it is pain.."</p>

<article class="abs service" style="left:86px">
  <div class="service-icon"><svg width="90" height="90" viewBox="0 0 90 90" fill="#fff"><path d="M45 12c-10 0-16 8-16 16h32c0-8-6-16-16-16z"/><rect x="43" y="4" width="4" height="10"/><rect x="18" y="30" width="54" height="6"/><rect x="22" y="38" width="6" height="30"/><rect x="34" y="38" width="6" height="30"/><rect x="50" y="38" width="6" height="30"/><rect x="62" y="38" width="6" height="30"/><rect x="14" y="70" width="62" height="8"/></svg></div>
  <h3>GOVT AGENCIES</h3>
  <p>Lorem Ipsum is simply dummy text of the printing and typesetting industry. Lorem Ipsum has been the industry's standard dummy text ever since the 1500s,</p>
  <span class="btn-more">Read More</span>
</article>
<article class="abs service is-active" style="left:436px">
  <div class="service-icon"><svg width="90" height="90" viewBox="0 0 90 90" fill="none" stroke="#fff" stroke-width="5"><rect x="10" y="40" width="70" height="8"/><path d="M16 48v30M74 48v30M54 48v30M54 58h20M54 68h20"/><rect x="22" y="12" width="28" height="22"/><path d="M36 34v6M60 40V20l10-8"/></svg></div>
  <h3>OFFICE</h3>
  <p>Lorem Ipsum is simply dummy text of the printing and typesetting industry. Lorem Ipsum has been the industry's standard dummy text ever since the 1500s,</p>
  <span class="btn-more">Read More</span>
</article>
<article class="abs service" style="left:786px">
  <div class="service-icon"><svg width="100" height="90" viewBox="0 0 100 90" fill="#fff"><path d="M50 8L4 46h12l34-28 34 28h12z"/><path d="M22 44L50 22l28 22v36H22z"/><rect x="44" y="54" width="12" height="26" fill="#c9c9c9"/></svg></div>
  <h3>HOME</h3>
  <p>Lorem Ipsum is simply dummy text of the printing and typesetting industry. Lorem Ipsum has been the industry's standard dummy text ever since the 1500s,</p>
  <span class="btn-more">Read More</span>
</article>

<section class="abs about" role="img" aria-label="Green-tinted photo of a gloved hand cleaning with a sponge">
  <h2 class="abs section-title">About Harbor Lane Services W.L.L</h2>
  <p class="abs quote">"Neque porro quisquam est qui dolorem ipsum quia dolor sit amet, consectetur, adipisci velit.."<br>"There is no one who loves pain itself, who seeks after it and wants to have it, simply because it is pain.."</p>
  <p class="abs about-text" style="top:222px">Contrary to popular belief, Lorem Ipsum is not simply random text. It has roots in a piece of classical Latin literature from 45 BC, making it over 2000 years old. Martin Ashby, a Latin professor at Westbrook College in Virginia, looked up one of the more obscure Latin words, consectetur, from a Lorem Ipsum passage, and going through the cites of the word in classical literature, discovered the undoubtable source. Lorem Ipsum comes from sections 1.10.32 and 1.10.33 of "de Finibus Bonorum et Malorum" (The Extremes of Good and Evil) by Aurelian, written in 45 BC. This book is a treatise on the theory of ethics, very popular during the Renaissance. The first line of Lorem Ipsum, "Lorem ipsum dolor sit amet..", comes from a line in section 1.10.32.</p>
  <p class="abs about-text" style="top:374px">The standard chunk of Lorem Ipsum used since the 1500s is reproduced below for those interested. Sections 1.10.32 and 1.10.33 from "de Finibus Bonorum et Malorum" by Aurelian are also reproduced in their exact original form, accompanied by English versions from the 1914 translation by J. Hollis.</p>
  <span class="abs btn-white">ABOUT ME</span>
</section>

<h2 class="abs section-title" style="top:2024px">Our News</h2>
<div class="abs title-rule" style="top:2084px"></div>

<article class="abs news-card" style="left:86px;width:482px">
  <div class="news-photo" role="img" aria-label="Photo of a cleaning staff member holding a broom" style="background:linear-gradient(135deg,#eeeeee,#d9c7cf 55%,#e8e8e8)">
    <span class="news-date"><b>30</b><small>May<br>2017</small></span>
  </div>
  <div class="news-body"><h4>The standard Lorem Ipsum passage, used</h4><p>Lorem Ipsum is simply dummy text of the printing and typesetting industry. Lorem Ipsum has been the industry's standard dummy text ever since the...</p></div>
</article>
<article class="abs news-card" style="left:622px;width:490px">
  <div class="news-photo" role="img" aria-label="Photo of a cleaning staff member with supplies" style="background:linear-gradient(135deg,#f2f2f2,#b9c4d6 50%,#d7c46a)">
    <span class="news-date" style="background:#222"><b>29</b><small>May<br>2017</small></span>
  </div>
  <div class="news-body"><h4>The standard Lorem Ipsum passage, used</h4><p>Lorem Ipsum is simply dummy text of the printing and typesetting industry. Lorem Ipsum has been the industry's standard dummy text ever since the...</p></div>
</article>

<footer class="abs site-footer">
  <h5 class="abs footer-head" style="left:88px;top:80px">Contact Information</h5>
  <div class="abs contact-item" style="top:136px"><span class="round"><svg width="16" height="20" viewBox="0 0 16 20"><path d="M8 1a6 6 0 0 0-6 6c0 5 6 12 6 12s6-7 6-12a6 6 0 0 0-6-6z" fill="#fff"/><circle cx="8" cy="7" r="2.2" fill="#2b2b2b"/></svg></span><span>42 Corniche Road, Riffa<br>Bahrain, 51947.</span></div>
  <div class="abs contact-item" style="top:208px"><span class="round"><svg width="18" height="14" viewBox="0 0 18 14"><rect width="18" height="14" rx="1" fill="#fff"/><path d="M1 1l8 7 8-7" stroke="#2b2b2b" stroke-width="1.5" fill="none"/></svg></span><span>hello@harborlane.example</span></div>
  <div class="abs contact-item" style="top:274px"><span class="round"><svg width="18" height="18" viewBox="0 0 18 18"><path d="M4 1c1 0 2 3 2 4s-2 1-1 3 3 4 5 5 2-1 3-1 4 1 4 2-2 3-4 3C7 17 1 11 1 5c0-2 2-4 3-4z" fill="#fff"/></svg></span><span>555-408-2291</span></div>
  <div class="abs social"><span></span><span></span><span></span><span></span></div>

  <h5 class="abs footer-head" style="left:470px;top:78px">Message Us</h5>
  <div class="abs field" style="left:470px;top:116px;width:320px">NAME :</div>
  <div class="abs field" style="left:796px;top:116px;width:318px">EMAIL:</div>
  <div class="abs field" style="left:470px;top:158px;width:644px">PHONE :</div>
  <div class="abs field" style="left:470px;top:200px;width:644px;height:86px">MESSAGE :</div>
  <span class="abs btn-submit">Submit</span>
</footer>

<div class="abs bottom-bar">
  <nav class="abs bottom-nav"><span>HOME</span><span>|</span><span>ABOUT US</span><span>|</span><span>STAFF</span><span>|</span><span>BLOG</span><span>|</span><span>CONTACTS</span></nav>
  <span class="abs copyright">Copyright © 2017. Harbor Lane Services W.L.L | All rights Reserved.</span>
</div>

</body>
</html>
```